Dental Practice Billboard Design

We are a newer dental practice in need of a simple but appealing billboard for our growing dental practice to attract new patients. The practice is owned by husband and wife dentists and is family friendly in a small town in Kentucky. We try to be very friendly and caring to our patients. Would prefer a blue background for the billboard and our tooth logo to be prominent. We are partial to the Patua One font used in the image below but please feel free to tweak it as you deem necessary. The shape of the uppercase D and lowercase g are why we like that font, so fonts with a similarly shaped “D” and “g” would work as well. Please include our phone number (555) 847-1390. Please see our website Harlowbrookdentistry.example for more info on the practice if needed. Thank you! Looking forward to seeing your creation.
Updates

The dimensions will be 12ft x 24ft (3.6576m x 7.3152m). Apologies for not including this in the original prompt. Thank you all for your submissions.

Industry/Entity Type

Dental

Font styles to use
Other font styles liked:
• Patua One

Colors
0054AA
0677BA
7BADD7
CADEEF
E8F1F8
0094D4
00A9DD
6FCCEA
C7EBF8
E9F6FB
00AB8E
00BBA5
67D7C9
C6EFE9
E9F9F6
59FF00
82FF00
B8FF75
E3FFCB
F4FFEA

Requirements
Must have
• Phone number, website, Logo, Practice name “Harlow Brook Dentistry”
Should not have
• A tagline or slogan

```html
<!DOCTYPE html>
<html lang="en">
<head>
<meta charset="utf-8">
<title>Harlow Brook Dentistry — Billboard</title>
<link href="https://fonts.googleapis.com/css2?family=Patua+One&family=Bree+Serif&display=swap" rel="stylesheet">
<style>
  :root {
    --navy: #062a5c;
    --green: #17b11c;
    --white: #ffffff;
    --paper: #ffffff;
    --ink: #333333;
    --rule: #c9d3e2;
  }
  * { margin: 0; padding: 0; box-sizing: border-box; }
  html, body {
    width: 1071px; height: 1200px; overflow: hidden;
    background: var(--paper);
  }
  .billboard {
    position: absolute;
    left: 35px; top: 350px;
    width: 1000px; height: 500px;
    background: var(--navy);
    overflow: hidden;
    font-family: "Bree Serif", serif;
    color: var(--white);
  }
  .brand {
    position: absolute;
    left: 0; top: 30px; width: 1000px;
    display: flex; align-items: center; justify-content: center; gap: 28px;
  }
  .brand-dot {
    width: 120px; height: 120px; border-radius: 50%;
    background: var(--green);
    flex: none;
  }
  .brand-name {
    font-family: "Patua One", serif;
    color: var(--white);
    line-height: 1;
  }
  .brand-name .line-main { display: block; font-size: 86px; }
  .brand-name .line-sub { display: block; font-size: 46px; margin-top: 10px; padding-left: 4px; }

  .services-heading {
    position: absolute; left: 0; top: 248px; width: 1000px;
    text-align: center;
    font-family: "Patua One", serif;
    font-size: 36px; line-height: 1;
    color: var(--green);
    letter-spacing: 0.5px;
  }
  .services-rule {
    position: absolute; top: 263px; height: 1px;
    background: var(--rule);
  }
  .services-rule.left { left: 57px; width: 293px; }
  .services-rule.right { left: 652px; width: 293px; }

  .service-column {
    position: absolute; top: 298px;
    list-style: none;
  }
  .service-column li {
    display: flex; align-items: center;
    height: 35px;
    font-size: 27px; line-height: 1;
  }
  .service-column .tick {
    width: 20px; height: 20px; margin-right: 8px; flex: none;
  }
  .col-1 { left: 44px; }
  .col-2 { left: 279px; }
  .col-3 { left: 534px; }
  .col-4 { left: 748px; }

  .contact-bar { position: absolute; left: 0; top: 420px; width: 1000px; height: 80px; }
  .website {
    position: absolute; left: 33px; top: 440px;
    display: flex; align-items: center; gap: 14px;
    font-size: 30px; color: var(--white); line-height: 1;
  }
  .website svg { width: 46px; height: 46px; flex: none; }
  .phone {
    position: absolute; left: 634px; top: 445px;
    display: flex; align-items: center; gap: 20px;
    font-size: 38px; color: var(--ink); line-height: 1;
  }
  .phone svg { width: 44px; height: 44px; flex: none; }
</style>
</head>
<body>
  <main class="billboard">
    <header class="brand">
      <div class="brand-dot" aria-hidden="true"></div>
      <h1 class="brand-name">
        <span class="line-main">Harlow Brook</span>
        <span class="line-sub">Dentistry</span>
      </h1>
    </header>

    <div class="services-rule left"></div>
    <h2 class="services-heading">OUR SERVICES</h2>
    <div class="services-rule right"></div>

    <svg width="0" height="0" style="position:absolute">
      <symbol id="tick" viewBox="0 0 20 20">
        <path d="M2 11 L8 17 L18 3" fill="none" stroke="#17b11c" stroke-width="2.4" stroke-linecap="round" stroke-linejoin="round"/>
      </symbol>
    </svg>

    <ul class="service-column col-1">
      <li><svg class="tick"><use href="#tick"/></svg>Crowns</li>
      <li><svg class="tick"><use href="#tick"/></svg>Root Canals</li>
      <li><svg class="tick"><use href="#tick"/></svg>Extractions</li>
    </ul>
    <ul class="service-column col-2">
      <li><svg class="tick"><use href="#tick"/></svg>Implants</li>
      <li><svg class="tick"><use href="#tick"/></svg>Bridges</li>
      <li><svg class="tick"><use href="#tick"/></svg>Clear Aligners</li>
    </ul>
    <ul class="service-column col-3">
      <li><svg class="tick"><use href="#tick"/></svg>Veneers</li>
      <li><svg class="tick"><use href="#tick"/></svg>Whitening</li>
      <li><svg class="tick"><use href="#tick"/></svg>Fillings</li>
    </ul>
    <ul class="service-column col-4">
      <li><svg class="tick"><use href="#tick"/></svg>Cleanings</li>
      <li><svg class="tick"><use href="#tick"/></svg>Dentures</li>
      <li><svg class="tick"><use href="#tick"/></svg>OverDentures</li>
    </ul>

    <svg class="contact-bar" viewBox="0 0 1000 80" aria-hidden="true">
      <polygon points="0,0 568,0 594,80 0,80" fill="#17b11c"/>
      <polygon points="580,15 1000,15 1000,80 602,80" fill="#ffffff"/>
    </svg>

    <div class="website">
      <svg viewBox="0 0 46 46" aria-hidden="true">
        <circle cx="23" cy="23" r="20" fill="none" stroke="#fff" stroke-width="3.5"/>
        <path d="M14 12 q6 -2 10 2 q-2 5 -7 5 q-2 4 2 8 q-1 5 -5 6 q-3 -6 -5 -10 q0 -7 5 -11z M28 24 q5 -1 8 3 q-2 7 -8 9 q-3 -6 0 -12z" fill="#fff"/>
      </svg>
      <span>Harlowbrookdentistry.example</span>
    </div>

    <div class="phone">
      <svg viewBox="0 0 44 44" aria-hidden="true">
        <path d="M9 5 l7 -1 l4 10 l-5 4 q3 8 11 12 l4 -5 l10 4 l-1 7 q-3 5 -9 4 q-14 -3 -23 -19 q-3 -9 2 -16z" fill="#17b11c"/>
        <path d="M25 6 q10 2 13 12" fill="none" stroke="#17b11c" stroke-width="3" stroke-linecap="round"/>
        <path d="M24 13 q6 1 7 7" fill="none" stroke="#17b11c" stroke-width="3" stroke-linecap="round"/>
      </svg>
      <span>(555) 847-1390</span>
    </div>
  </main>
</body>
</html>
```